Open Harbor book needs a cover design

I need a front and back cover design that demonstrates a strong sense of possibility that trust can be repaired even if things look bleak. Repairing trust is difficult, but this book is full of wisdom, proven strategies, and doctoral research to help people strengthen relationships and improve trust. It can help any group: business, nonprofit, education, service. Showing diversity of groups and people is very important. For the cover title, there should be a play on words: "Open Harbor: Is it? Within Reach" should have the words "is it?" crossed out and the words "It IS! should be replaced there in a striking way. Perhaps in red ink. For publishing purposes, book will be titled Open Harbor: It IS Within Reach! Please see the attachment for an example. The book layout is approximately 260 pages.

A business self-help book, but the target is any person in a group that feels they have lost trust in each other. It can be just a normal person struggling in a volunteer group they are a part of, or a supervisor whose group is not working well together. It can be a leader who just wants their group to be stronger.

Business Management

• Allise - I believe is being used on the interior of the book for the title page and headings

• Show hope and possibility in the midst of difficulty. Must have a play on the words in the title "Open Harbor: Is it? Within Reach" with crossing out "is it?" with "It IS!" (see attached example) Must include the author's name: Marla Quentin, PhD Must include a smaller tagline: "Practical Steps to Move Teams Forward Again"
• Showing diverse people, or hands. Diverse kinds of groups - not just business. A colorful cover. Maybe show the complexity of trust when it is broken...broken pieces of trust that are then picked up and put together when people work together. Could show people (or images of hands) or other ways to show that it's a choice and it is possible to repair broken trust. I'd also like to convey a sense of a group - not just random people. That they have something at stake to work on repairing trust together and this book can help them.
• If images of people are used, just showing one gender or race is not okay. Nor just binary choices: like an image containing one man and one woman, or one white person and one person of color - otherwise it seems that the book on Open Harbor is about race or gender relations.

```html
<!DOCTYPE html>
<html lang="en">
<head>
<meta charset="UTF-8">
<title>Open Harbor — Book Cover</title>
<link rel="stylesheet" href="https://fonts.googleapis.com/css2?family=Federo&family=Yanone+Kaffeesatz:wght@300;400&display=swap">
<style>
  :root {
    --backdrop: #e9e6e2;
    --cover-white: #ffffff;
    --title-navy: #141a2b;
    --title-teal: #2fb0c9;
    --band-teal: #2fa9c6;
    --ink-dark: #1c1c1c;
    --rule-grey: #6f6f6f;
    --strike-red: #d3202a;
    --author-white: #ffffff;
  }
  * { margin: 0; padding: 0; box-sizing: border-box; }
  html, body {
    width: 1200px;
    height: 800px;
    overflow: hidden;
    background: var(--backdrop);
  }
  .canvas {
    position: relative;
    width: 1200px;
    height: 800px;
    display: flex;
    align-items: center;
    justify-content: center;
  }
  .cover {
    position: relative;
    width: 480px;
    height: 728px;
    background: var(--cover-white);
    box-shadow: 0 6px 24px rgba(0,0,0,0.18);
    overflow: hidden;
  }
  .title {
    position: absolute;
    top: 22px;
    left: 0;
    right: 0;
    text-align: center;
    font-family: "Federo", sans-serif;
    line-height: 0.92;
  }
  .title-line {
    display: block;
    font-size: 112px;
    letter-spacing: -2px;
  }
  .title-line--first { color: var(--title-navy); }
  .title-line--second { color: var(--title-teal); font-size: 104px; }

  .hands-photo {
    position: absolute;
    top: 232px;
    left: 40px;
    width: 400px;
    height: 330px;
    background:
      radial-gradient(ellipse 42% 40% at 50% 50%, #ffffff 0%, #ffffff 45%, rgba(255,255,255,0) 72%),
      radial-gradient(ellipse 60% 55% at 50% 50%, #a7785a 0%, #d9b39a 40%, #ece6e2 70%, rgba(255,255,255,0) 100%);
  }
  .wordplay {
    position: absolute;
    top: 330px;
    left: 0;
    right: 0;
    text-align: center;
    font-family: "Yanone Kaffeesatz", sans-serif;
    color: var(--ink-dark);
    line-height: 1;
  }
  .wordplay-answer { display: block; font-size: 40px; font-weight: 400; }
  .wordplay-question {
    display: inline-block;
    position: relative;
    font-size: 25px;
    font-weight: 300;
    margin: 2px 0 4px;
  }
  .wordplay-strike {
    position: absolute;
    left: -4px;
    top: 0;
    width: calc(100% + 8px);
    height: 100%;
  }
  .wordplay-promise { display: block; font-size: 40px; font-weight: 400; }

  .tagline {
    position: absolute;
    top: 580px;
    left: 84px;
    right: 84px;
    border-top: 1px solid var(--rule-grey);
    border-bottom: 1px solid var(--rule-grey);
    padding: 6px 0 5px;
    text-align: center;
    font-family: "Yanone Kaffeesatz", sans-serif;
    font-weight: 300;
    font-size: 22px;
    line-height: 1.1;
    color: var(--ink-dark);
    text-transform: uppercase;
  }
  .author-band {
    position: absolute;
    left: 0;
    right: 0;
    bottom: 0;
    height: 60px;
    background: var(--band-teal);
    border-top: 3px solid var(--cover-white);
    box-shadow: 0 -3px 0 var(--band-teal);
    display: flex;
    align-items: center;
    justify-content: center;
    font-family: "Yanone Kaffeesatz", sans-serif;
    font-weight: 400;
    font-size: 30px;
    color: var(--author-white);
  }
</style>
</head>
<body>
  <main class="canvas">
    <section class="cover" aria-label="Open Harbor book cover">
      <h1 class="title">
        <span class="title-line title-line--first">OPEN</span>
        <span class="title-line title-line--second">HARBOR</span>
      </h1>

      <div class="hands-photo" role="img" aria-label="Photograph of diverse hands clasping one another's wrists in a connected circle"></div>

      <p class="wordplay">
        <span class="wordplay-answer">It Is!</span>
        <span class="wordplay-question">Is it?
          <svg class="wordplay-strike" viewBox="0 0 100 40" preserveAspectRatio="none" aria-hidden="true">
            <line x1="0" y1="12" x2="100" y2="30" stroke="#d3202a" stroke-width="4"/>
            <line x1="0" y1="30" x2="100" y2="12" stroke="#d3202a" stroke-width="4"/>
          </svg>
        </span>
        <span class="wordplay-promise">Within Reach</span>
      </p>

      <p class="tagline">Practical Steps to Move<br>Teams Forward Again</p>

      <footer class="author-band">Marla Quentin, PhD</footer>
    </section>
  </main>
</body>
</html>
```